Professional Photography Business cards

I need business cards that include my logo which I have uploaded. I run a photography business. I am open to ideas but I would like one side to have my logo and the other side to have my contact info. I don't have a website made but I do own a website domain. I have uploaded 2 different logo color schemes. My business colors are Blue, black , and white.

Business Name
Business Phone Number
Business Email
Business Website address
Instagram

Industry/Entity Type

Professional Photography

Contact Information for Business Card

Phone Number: 916-384-7702 email: info@tlane-studio.example Instagram: @t.lanestudio website doman- www.tlane-studio.example

Requirements
Must have
• I like the idea of a business card with a full black background front and back of card. My colors must include royal blue, black, and white

```html
<!DOCTYPE html>
<html lang="en">
<head>
<meta charset="utf-8">
<title>T. Lane Studio – Business Cards</title>
<link href="https://fonts.googleapis.com/css2?family=Arimo:wght@400&display=swap" rel="stylesheet">
<style>
  :root {
    --bg: #2a2a2a;
    --card: #060606;
    --royal: #1a1fc4;
    --white: #ffffff;
    --rule: #3a3a3a;
  }
  * { box-sizing: border-box; margin: 0; padding: 0; }
  html, body {
    width: 1200px; height: 900px; overflow: hidden;
    background: var(--bg);
    font-family: "Arimo", Arial, sans-serif;
  }
  .sheet {
    width: 1200px; height: 900px;
    display: flex; align-items: center; justify-content: center; gap: 40px;
  }
  .card {
    width: 540px; height: 309px;
    background: var(--card);
    position: relative;
  }
  .brand {
    display: flex; align-items: center; gap: 14px;
  }
  .brand-dot {
    width: 44px; height: 44px; border-radius: 50%;
    border: 3px solid var(--white);
  }
  .brand-name {
    color: var(--royal);
    font-size: 30px; font-weight: 400; letter-spacing: 2px;
    white-space: nowrap;
  }
  .card--contact .brand {
    position: absolute; left: 40px; top: 50%; transform: translateY(-50%);
  }
  .card--contact .brand-name { font-size: 22px; }
  .card--contact .brand-dot { width: 34px; height: 34px; }
  .divider {
    position: absolute; left: 262px; top: 84px; bottom: 84px;
    width: 1px; background: var(--rule);
  }
  .contact-list {
    position: absolute; left: 284px; top: 50%; transform: translateY(-50%);
    list-style: none; color: var(--white); font-size: 14px;
  }
  .contact-list li {
    display: flex; align-items: center; gap: 9px; line-height: 22px;
    white-space: nowrap;
  }
  .contact-list li.social { margin-top: 18px; font-size: 15px; }
  .icon { width: 14px; height: 14px; flex: none; }
  .social-mark {
    width: 15px; height: 15px; border-radius: 50%;
    border: 1.5px solid var(--royal); flex: none;
  }
  .card--logo {
    display: flex; align-items: center; justify-content: center;
  }
  .card--logo .brand-name { font-size: 40px; }
  .card--logo .brand-dot { width: 58px; height: 58px; border-width: 4px; }
</style>
</head>
<body>
<main class="sheet">
  <section class="card card--contact" aria-label="Contact side">
    <div class="brand">
      <span class="brand-dot"></span>
      <span class="brand-name">T. Lane Studio</span>
    </div>
    <div class="divider"></div>
    <ul class="contact-list">
      <li>
        <svg class="icon" viewBox="0 0 16 16" aria-hidden="true"><path fill="var(--royal)" d="M3.6 1.5l2.3 2.6-1.3 1.6c.9 2 2.5 3.6 4.7 4.7l1.6-1.3 2.6 2.3-1.4 2.1C6.900 14.4 1.600 9.100 1.500 2.900z"/></svg>
        <span>916-384-7702</span>
      </li>
      <li>
        <svg class="icon" viewBox="0 0 16 16" aria-hidden="true"><rect x="1" y="3" width="14" height="10" fill="var(--royal)"/><path d="M1 3l7 6 7-6" stroke="var(--card)" stroke-width="1.3" fill="none"/></svg>
        <span>info@tlane-studio.example</span>
      </li>
      <li>
        <svg class="icon" viewBox="0 0 16 16" aria-hidden="true"><g fill="none" stroke="var(--royal)" stroke-width="1.4"><circle cx="8" cy="8" r="6.5"/><ellipse cx="8" cy="8" rx="2.8" ry="6.5"/><path d="M1.5 8h13"/></g></svg>
        <span>www.tlane-studio.example</span>
      </li>
      <li class="social">
        <span class="social-mark"></span>
        <span>@t.lanestudio</span>
      </li>
    </ul>
  </section>

  <section class="card card--logo" aria-label="Logo side">
    <div class="brand">
      <span class="brand-name">T. Lane Studio</span>
      <span class="brand-dot"></span>
    </div>
  </section>
</main>
</body>
</html>
```